verdant terraces simple classy business card design

my name is colin barrow and I run a gardening business aimed at high class verdant terraces. the business name is verdant terraces and our logo was designed on pixel harbour .My clientel are anything from residential homes to businesses. I take pride in my work and know that I offer a service like no other in my area.
The business card will be used to represent my business and I want it to be not only rememberable, but simplistic and modern. Eye catching too. Of course I would like it relatable to gardening and appealing to the correct clientel - those being garden enthusiasts, prestigious homes and businesses that are after top of the line gardening services like no other on the market.
I am not a typical lawn mowing business so I don't want a typical card design that represents that. The gardens I work with are generally million dollar properties with owners who are very garden proud looking for upkeep and guidance from me along with sometimes whole new garden designs. I want the business cards to show to my clients that I take pride, as they do, in their garden. And I want them to know from my card that I am a professional, qualified horticulturist offering them a top of the line service for life. I want them to refer my business on. I want them to look at my business card and see class and professionalism in a modern unique bold way.
The card should be simple with the possibility of the logo on the front being embossed/debossed and my details on the back the card should have a organic garden feel it's very important to me that it is absolutely perfect
I am also very open to ideas and suggestions so look forward to seeing the designs. the business logo has been supplied with this project and I want the card to be double sided

Contact info is
Colin Barrow - Managing Director / Horticulturist
Phone : 0481 526 704
Email: colinbarrow@verdantterraces.example.au

Target Market(s)

high class gardens residential and commercial

Industry/Entity Type

Gardener

Contact Information for Business Card

Contact info is
Phone : 0481 526 704

PLEASE MAKE CARD DOUBLE SIDED

Requirements
Must have
• organic simple classy modern feel
• must flow with the current logo that has been supplied with this project
• Double sided
• Must explain in a simple way that I deal with high end gardens and I'm a qualified horticulturist
Nice to have
• embossed debossed logo
Should not have
• shouldn't be to busy or cheap looking

```html
<!DOCTYPE html>
<html lang="en">
<head>
<meta charset="utf-8">
<title>Verdant Terraces – Business Card</title>
<link rel="stylesheet" href="https://fonts.googleapis.com/css2?family=Open+Sans:wght@400;600;700&display=swap">
<style>
  :root {
    --backdrop: #e9e4dc;
    --card-stock: #f6f5f1;
    --card-edge: #dcd9d2;
    --leaf-green: #5aa845;
    --leaf-green-soft: #cfe5c6;
    --ink: #3d3d3d;
    --ink-soft: #555555;
  }
  * { box-sizing: border-box; margin: 0; padding: 0; }
  html, body {
    width: 1200px;
    height: 794px;
    overflow: hidden;
    background: var(--backdrop);
    font-family: "Open Sans", Arial, sans-serif;
  }
  .canvas {
    position: relative;
    width: 1200px;
    height: 794px;
  }
  .card {
    position: absolute;
    width: 540px;
    height: 328px;
    background: var(--card-stock);
    border: 1px solid var(--card-edge);
    border-radius: 3px;
    box-shadow: 0 6px 18px rgba(0,0,0,0.12);
  }
  .card--details { left: 80px; top: 70px; }
  .card--brand { left: 580px; top: 396px; }

  /* details side */
  .brand-mark-area {
    position: absolute;
    right: 60px;
    top: 34px;
    width: 180px;
    height: 180px;
    border-radius: 50%;
    background: var(--leaf-green-soft);
  }
  .contact {
    position: absolute;
    left: 56px;
    top: 166px;
    width: 300px;
  }
  .contact__name {
    color: var(--leaf-green);
    font-weight: 700;
    font-size: 17px;
    letter-spacing: 0.5px;
    line-height: 1.1;
  }
  .contact__role {
    color: var(--ink);
    font-size: 12.5px;
    font-weight: 600;
    line-height: 1.35;
    margin-top: 2px;
    text-transform: uppercase;
  }
  .contact__rule {
    height: 2px;
    background: var(--leaf-green);
    width: 290px;
    margin: 8px 0 9px;
  }
  .contact__line {
    color: var(--ink-soft);
    font-size: 12.5px;
    line-height: 1.45;
  }
  .contact__label {
    color: var(--leaf-green);
    font-weight: 700;
  }

  /* brand side */
  .brand-lockup {
    position: absolute;
    left: 0;
    right: 0;
    top: 132px;
    display: flex;
    align-items: center;
    justify-content: center;
    gap: 14px;
  }
  .brand-lockup__dot {
    width: 30px;
    height: 30px;
    border-radius: 50%;
    background: var(--leaf-green);
  }
  .brand-lockup__name {
    color: var(--leaf-green);
    font-weight: 600;
    font-size: 34px;
    letter-spacing: 3px;
    text-transform: uppercase;
  }
</style>
</head>
<body>
<main class="canvas">
  <section class="card card--details" aria-label="Card back with contact details">
    <div class="brand-mark-area" role="img" aria-label="Company emblem placement"></div>
    <div class="contact">
      <p class="contact__name">COLIN BARROW</p>
      <p class="contact__role">Managing Director<br>Horticulturist</p>
      <div class="contact__rule"></div>
      <p class="contact__line"><span class="contact__label">Phone</span> : 0481 526 704</p>
      <p class="contact__line">colinbarrow@verdantterraces.example.au</p>
      <p class="contact__line">www.verdantterraces.example.au</p>
    </div>
  </section>

  <section class="card card--brand" aria-label="Card front with company name">
    <div class="brand-lockup">
      <span class="brand-lockup__dot"></span>
      <span class="brand-lockup__name">Verdant Terraces</span>
    </div>
  </section>
</main>
</body>
</html>
```